Scientific Web Site for KLORVEST

Professional Scientific / Service orientated web site, motto, new logos attached for viewing.

"We measure so the Business Owner can Manage" their environments.
Site needs to be be mobile friendly.

We provide a service to electronically measure cleanliness of any surface and a value added disinfecting fogging surface.

Reports showing locations, trending, tracking and randomized test plans ongoing audits will be made available..

NOTE: Although image of Corona Virus is current we don't wont it plastered through the web site, their is more than the current virus.

Home Page - Professional Scientific / Service Looking
About
Our Approach
Services
Residential
Commercial
Transportation
Gyms
Educational & Daycare
Real Estate - Open for inspections, End of Lease etc

Contact
Mobile #
Email
Form to leave their details

Links to social media, Facebook, Instagram
Reference Sites: Ranked in preference
www.brelmont.com.au
https://www.tidewellhygiene.co.uk/
https://www.mistrova.com/
https://www.zenplax.com.au/specialist-surface-disinfection/
https://www.artfolder.example/design/48172039
https://www.artfolder.example/design/51904476
https://www.artfolder.example/design/47318865

Target Market(s)

Commercial and professional Services

Font styles to use
Sans Serif

Requirements
Must have
• Wix Website
Clean fresh look with appropriate imaging
Web site is a company advertising that will hold static information and we will market through social media.
Nice to have
• Scientific look and feel
Should not have
• Prominent Corona Virus images or references

```html
<!DOCTYPE html>
<html lang="en">
<head>
<meta charset="utf-8">
<title>KLORVEST – Electronically Measure Cleanliness</title>
<link href="https://fonts.googleapis.com/css2?family=Poppins:ital,wght@0,400;0,500;0,600;0,700;0,800;1,400&display=swap" rel="stylesheet">
<style>
:root{
  --orange:#f07a1a;
  --orange-deep:#d9600c;
  --black:#000;
  --ink:#222;
  --grey-text:#666;
  --light:#f6f6f6;
  --footer:#231f20;
  --white:#fff;
}
*{margin:0;padding:0;box-sizing:border-box}
html,body{width:1200px;height:4202px;overflow:hidden}
body{position:relative;font-family:"Poppins",sans-serif;color:var(--ink);background:var(--white)}
.abs{position:absolute}

/* header */
.site-header{left:0;top:0;width:1200px;height:122px;background:var(--black)}
.brand{left:126px;top:44px;color:var(--white);font-size:26px;font-weight:600;letter-spacing:3px}
.brand-dot{left:102px;top:53px;width:14px;height:14px;border-radius:50%;background:var(--orange)}
.main-nav{left:468px;top:53px;display:flex;gap:22px;font-size:14px;color:var(--white)}
.main-nav .active{color:var(--orange)}
.header-phone{left:956px;top:50px;display:flex;align-items:center;gap:10px;color:var(--white);font-size:14px;font-weight:700}

/* hero */
.hero{left:0;top:122px;width:1200px;height:547px;background:linear-gradient(100deg,#7a3408 0%,#c85a10 35%,#f08a2a 60%,#e06a14 100%)}
.hero-title{left:126px;top:214px;color:var(--white);font-size:54px;font-weight:800;line-height:63px;letter-spacing:-1px}
.hero-text{left:128px;top:432px;width:380px;color:var(--white);font-size:17px;line-height:27px}
.hero-dots{left:126px;top:547px;display:flex;gap:20px;align-items:center}
.hero-dots span{width:7px;height:7px;border-radius:50%;background:var(--white)}
.hero-dots .on{width:14px;height:14px;border:2px solid var(--white);background:none;position:relative}
.hero-dots .on::after{content:"";position:absolute;left:2px;top:2px;width:6px;height:6px;border-radius:50%;background:var(--white)}

.section-title{color:var(--orange);font-size:33px;font-weight:700;left:0;width:1200px;text-align:center}
.section-text{left:240px;width:720px;text-align:center;font-size:12.5px;line-height:23px;color:var(--grey-text)}
.pill-btn{background:var(--orange);color:var(--white);border-radius:30px;font-size:12px;font-weight:500;display:flex;align-items:center;justify-content:center}

/* approach */
.approach-side{left:0;top:1067px;width:600px;height:517px;background:linear-gradient(180deg,#3c3c3e,#5a5a5c 60%,#6a6a6c)}
.approach-photo{left:600px;top:1067px;width:600px;height:517px;background:linear-gradient(120deg,#f5a15a,#ef7f22 50%,#c85a10)}
.approach-title{left:130px;top:1220px;color:var(--white);font-size:33px;font-weight:700}
.approach-text{left:132px;top:1282px;width:420px;color:var(--white);font-size:12.5px;line-height:23px}
.approach-note{left:134px;top:1362px;width:260px;color:var(--white);font-size:12px;font-style:italic;line-height:23px}

/* services */
.measure-pill{left:225px;top:1867px;width:749px;height:183px;border-radius:92px;background:var(--light)}
.measure-title{left:0;width:1200px;top:1921px;text-align:center;font-size:16px;font-weight:600;color:#444}
.icon-ring{width:74px;height:74px;border-radius:50%;border:2px solid var(--orange);background:var(--white);display:flex;align-items:center;justify-content:center}
.service-head{font-size:17px;font-weight:600;color:#444}
.service-text{width:270px;font-size:12px;line-height:23px;color:var(--grey-text)}
.right{text-align:right}

/* areas */
.areas{left:0;top:2614px;width:1200px;height:455px;background:linear-gradient(180deg,#f28a2e,#e8711a 55%,#cf5e10)}
.areas-title{left:0;width:1200px;top:2658px;text-align:center;color:var(--white);font-size:33px;font-weight:700}
.area-card{top:2745px;width:276px;height:259px;background:var(--white)}
.area-img{width:276px;height:139px}
.area-name{margin:22px 0 0 38px;color:var(--orange);font-size:17px;font-weight:700}
.area-text{margin:6px 0 0 38px;width:200px;font-size:12px;line-height:22px;color:var(--grey-text)}

/* contact */
.field{height:42px;border:1px solid #ddd;border-radius:22px;padding-left:20px;font-size:12px;color:#777;display:flex;align-items:center}

/* footer */
.site-footer{left:0;top:3696px;width:1200px;height:506px;background:var(--footer)}
.foot-head{top:3780px;color:var(--white);font-size:16px;font-weight:600}
.foot-list{list-style:none;color:#ccc;font-size:12.5px}
.foot-list li{height:29px;display:flex;align-items:center;gap:14px}
.foot-contact{color:#ccc;font-size:13px;line-height:18px}
.social{width:30px;height:30px;border-radius:50%;background:var(--white)}
.copyright{left:0;width:1200px;top:4150px;text-align:center;font-size:10px;color:#777}
</style>
</head>
<body>

<header class="abs site-header">
  <span class="abs brand-dot"></span>
  <div class="abs brand">KLORVEST</div>
  <nav class="abs main-nav">
    <span class="active">Home</span><span>About</span><span>Our Approach</span><span>Our Services</span><span>Contact</span>
  </nav>
  <div class="abs header-phone">
    <svg width="18" height="18" viewBox="0 0 24 24" fill="none" stroke="#f07a1a" stroke-width="2"><path d="M5 3h4l2 5-3 2a11 11 0 0 0 6 6l2-3 5 2v4a2 2 0 0 1-2 2A17 17 0 0 1 3 5a2 2 0 0 1 2-2z"/></svg>
    123-456-7890
  </div>
</header>

<section class="abs hero" role="img" aria-label="Orange-toned scientific image of a DNA helix beside a microscopic cell"></section>
<h1 class="abs hero-title">Electronically<br>Measure<br>Cleanliness</h1>
<p class="abs hero-text">We provide a service to electronically measure cleanliness of any surface and a value added disinfecting fogging surface.</p>
<div class="abs hero-dots"><span class="on"></span><span></span><span></span></div>

<h2 class="abs section-title" style="top:768px">ABOUT COMPANY</h2>
<p class="abs section-text" style="top:840px">Sed ut perspiciatis unde omnis iste natus error sit voluptatem accusantium doloremque laudantium.Sed ut perspiciatis unde omnis iste natus error sit voluptatem accusantium doloremque laudantium.Sed ut perspiciatis unde omnis iste natus error sit voluptatem accusantium doloremque ium.doloremque</p>
<div class="abs pill-btn" style="left:536px;top:940px;width:130px;height:38px">View More</div>

<div class="abs approach-side" role="img" aria-label="Dim grey laboratory background with test tubes"></div>
<div class="abs approach-photo" role="img" aria-label="Orange-toned photo of a scientist working at a microscope"></div>
<h2 class="abs approach-title">OUR APPROACH</h2>
<p class="abs approach-text">Sed ut perspiciatis unde omnis iste natus error sit voluptatem accusantium doloremque laudantium.</p>
<p class="abs approach-note">Locations, Trending, Tracking and Randomized test plans ongoing audits will be made available..</p>

<h2 class="abs section-title" style="top:1654px">OUR SERVICES</h2>
<p class="abs section-text" style="top:1728px">Sed ut perspiciatis unde omnis iste natus error sit voluptatem accusantium doloremque laudantium.Sed ut perspiciatis unde omnis iste natus error sit voluptatem accusantium doloremque laudant</p>

<div class="abs measure-pill"></div>
<div class="abs icon-ring" style="left:563px;top:1814px">
  <svg width="40" height="40" viewBox="0 0 40 40" fill="none" stroke="#f07a1a" stroke-width="2"><circle cx="17" cy="17" r="10"/><line x1="24" y1="24" x2="33" y2="33"/></svg>
</div>
<div class="abs measure-title">WE MEASURE SO YOU CAN MANAGE</div>
<p class="abs section-text" style="top:1961px">Sed ut perspiciatis unde omnis iste natus error sit voluptatem accusantium doloremque laudantium.Sed ut perspiciatis unde omnis iste natus error sit voluptatem accusantium doloremque laudant</p>

<svg class="abs" style="left:400px;top:2080px" width="400" height="400" viewBox="0 0 400 400">
  <circle cx="199" cy="199" r="173" fill="none" stroke="#999" stroke-width="1.5" stroke-dasharray="6 6"/>
  <circle cx="199" cy="199" r="146" fill="#f4f4f4" stroke="#f07a1a" stroke-width="5"/>
  <circle cx="199" cy="26" r="8" fill="#f07a1a"/>
  <circle cx="38" cy="125" r="8" fill="#f07a1a"/>
  <circle cx="360" cy="125" r="8" fill="#f07a1a"/>
  <circle cx="56" cy="299" r="8" fill="#f07a1a"/>
  <circle cx="333" cy="314" r="8" fill="#f07a1a"/>
  <text x="199" y="208" text-anchor="middle" font-family="Poppins,sans-serif" font-weight="600" font-size="30" fill="#222" letter-spacing="2">KLORVEST</text>
</svg>

<div class="abs icon-ring" style="left:332px;top:2152px"><svg width="36" height="36" viewBox="0 0 36 36" fill="none" stroke="#f07a1a" stroke-width="2"><rect x="8" y="24" width="20" height="4"/><line x1="18" y1="24" x2="18" y2="8"/><circle cx="18" cy="8" r="3"/></svg></div>
<div class="abs service-head right" style="left:100px;width:215px;top:2193px">RESIDENTIAL</div>
<p class="abs service-text right" style="left:118px;top:2236px">Sed ut perspiciatis unde omnis iste natus error sit voluptatem accusantium dolorem-que laudantium.</p>

<div class="abs icon-ring" style="left:800px;top:2152px"><svg width="36" height="36" viewBox="0 0 36 36" fill="none" stroke="#f07a1a" stroke-width="2"><rect x="5" y="6" width="26" height="18"/><line x1="18" y1="24" x2="18" y2="30"/><line x1="11" y1="30" x2="25" y2="30"/></svg></div>
<div class="abs service-head" style="left:895px;top:2193px">COMMERCIAL</div>
<p class="abs service-text" style="left:809px;top:2236px">Sed ut perspiciatis unde omnis iste natus error sit voluptatem accusantium dolorem-que laudantium.</p>

<div class="abs icon-ring" style="left:346px;top:2372px"><svg width="36" height="36" viewBox="0 0 36 36" fill="none" stroke="#f07a1a" stroke-width="2"><path d="M12 5c0 9 12 17 12 26M24 5c0 9-12 17-12 26"/><line x1="13" y1="12" x2="23" y2="12"/><line x1="13" y1="24" x2="23" y2="24"/></svg></div>
<div class="abs service-head right" style="left:100px;width:229px;top:2413px">TRANSPORTATION</div>
<p class="abs service-text right" style="left:132px;top:2456px">Sed ut perspiciatis unde omnis iste natus error sit voluptatem accusantium dolorem-que laudantium.</p>

<div class="abs icon-ring" style="left:772px;top:2372px"><svg width="36" height="36" viewBox="0 0 36 36" fill="none" stroke="#f07a1a" stroke-width="2"><rect x="8" y="6" width="20" height="25"/><line x1="12" y1="14" x2="24" y2="14"/><line x1="12" y1="19" x2="24" y2="19"/><line x1="12" y1="24" x2="24" y2="24"/></svg></div>
<div class="abs service-head" style="left:866px;top:2413px">GYMS</div>
<p class="abs service-text" style="left:780px;top:2456px">Sed ut perspiciatis unde omnis iste natus error sit voluptatem accusantium dolorem-que laudantium.</p>

<section class="abs areas" role="img" aria-label="Orange background with faint network lines and a keyboard"></section>
<h2 class="abs areas-title">AREAS WE SERVE</h2>
<article class="abs area-card" style="left:148px">
  <div class="area-img" role="img" aria-label="Hands using a digital tablet" style="background:linear-gradient(135deg,#c9cdd6,#8c93a5)"></div>
  <h3 class="area-name">COMMERCIAL</h3>
  <p class="area-text">Sed ut perspiciatis unde omnis iste natus error sit</p>
</article>
<article class="abs area-card" style="left:468px">
  <div class="area-img" role="img" aria-label="Laboratory sample under light" style="background:linear-gradient(135deg,#4a4a4a,#b5a89a)"></div>
  <h3 class="area-name">RESIDENTIAL</h3>
  <p class="area-text">Sed ut perspiciatis unde omnis iste natus error sit</p>
</article>
<article class="abs area-card" style="left:791px">
  <div class="area-img" role="img" aria-label="Scientists examining a sample in a lab" style="background:linear-gradient(135deg,#e8ecf2,#8a7fa8)"></div>
  <h3 class="area-name">TRANSPORTATION</h3>
  <p class="area-text">Sed ut perspiciatis unde omnis iste natus error sit</p>
</article>

<h2 class="abs section-title" style="top:3159px">CONTACT FORM</h2>
<p class="abs section-text" style="top:3231px">Sed ut perspiciatis unde omnis iste natus error sit voluptatem accusantium doloremque laudantium.Sed ut perspiciatis unde omnis iste natus error sit voluptatem accusantium doloremque laudant</p>
<div class="abs field" style="left:194px;top:3311px;width:392px">Name</div>
<div class="abs field" style="left:612px;top:3311px;width:392px">Email</div>
<div class="abs field" style="left:194px;top:3383px;width:392px">Phone</div>
<div class="abs field" style="left:612px;top:3383px;width:392px">Subject</div>
<div class="abs field" style="left:194px;top:3453px;width:810px;height:96px;border-radius:48px;align-items:flex-start;padding-top:38px">Message</div>
<div class="abs pill-btn" style="left:424px;top:3574px;width:351px;height:42px">Submit Now</div>

<footer class="abs site-footer"></footer>
<div class="abs foot-head" style="left:161px">Get in Touch</div>
<div class="abs foot-head" style="left:432px">Quick Links</div>
<div class="abs foot-head" style="left:641px">Our Services</div>

<svg class="abs" style="left:163px;top:3850px" width="30" height="22" viewBox="0 0 30 22" fill="none" stroke="#999" stroke-width="1.5"><rect x="1" y="1" width="28" height="20"/><path d="M1 1l14 11L29 1"/></svg>
<div class="abs foot-contact" style="left:225px;top:3848px">info@mail.com<br>info@klorvest.com</div>
<svg class="abs" style="left:165px;top:3916px" width="20" height="30" viewBox="0 0 20 30" fill="none" stroke="#999" stroke-width="1.5"><rect x="1" y="1" width="18" height="28" rx="2"/><line x1="1" y1="24" x2="19" y2="24"/></svg>
<div class="abs foot-contact" style="left:222px;top:3918px">+123 456 7890<br>+123 456 7890</div>
<svg class="abs" style="left:162px;top:3990px" width="28" height="32" viewBox="0 0 28 32" fill="none" stroke="#999" stroke-width="1.5"><path d="M14 30s10-10 10-18a10 10 0 0 0-20 0c0 8 10 18 10 18z"/><circle cx="14" cy="12" r="4"/></svg>
<div class="abs foot-contact" style="left:225px;top:3994px">123, Main Road, New<br>City, My Country 123456</div>

<ul class="abs foot-list" style="left:436px;top:3840px">
  <li>&rarr;<span>About us</span></li><li>&rarr;<span>Blog</span></li><li>&rarr;<span>Contact us</span></li><li>&rarr;<span>Faq</span></li><li>&rarr;<span>Insurance</span></li><li>&rarr;<span>Contact us</span></li>
</ul>
<ul class="abs foot-list" style="left:638px;top:3840px">
  <li>&rarr;<span>Residential</span></li><li>&rarr;<span>Commercial</span></li><li>&rarr;<span>Transportation</span></li><li>&rarr;<span>Gyms</span></li><li>&rarr;<span>Educational &amp; Daycare</span></li><li>&rarr;<span>Real Estate</span></li>
</ul>

<div class="abs brand" style="left:908px;top:3852px;font-size:24px">KLORVEST</div>
<div class="abs social" style="left:952px;top:3920px" aria-label="Social profile link"></div>
<div class="abs social" style="left:989px;top:3920px" aria-label="Social profile link"></div>

<div class="abs copyright">©2020 Klorvest. All rights reserved.</div>
</body>
</html>
```